Marwick Law Letterhead

We need a new letterhead design for a Law Firm. The address for the law firm is 1475 Calloway Street, Suite 210, Houston, Texas 77041. Phone Number: 832-361-9027; Fax Number: 832-614-7359. The logo is uploaded to the project.

```html
<!DOCTYPE html>
<html lang="en">
<head>
<meta charset="utf-8">
<title>Marwick Law Letterhead</title>
<link href="https://fonts.googleapis.com/css2?family=Mulish:wght@400;500;700&display=swap" rel="stylesheet">
<style>
  :root {
    --backdrop: #e8e8e8;
    --paper: #ffffff;
    --navy: #1f2f5c;
    --red: #c4161c;
    --ink: #2a2a2a;
    --signature-tone: #d9d9d9;
  }
  html, body {
    margin: 0;
    padding: 0;
    width: 1154px;
    height: 1200px;
    overflow: hidden;
    background: var(--backdrop);
  }
  .canvas {
    position: relative;
    width: 1154px;
    height: 1200px;
    overflow: hidden;
  }
  .letterhead {
    position: absolute;
    left: 166px;
    top: 27px;
    width: 1066px;
    height: 1490px;
    background: var(--paper);
    transform: scale(0.77);
    transform-origin: top left;
    box-shadow: 0 6px 30px rgba(0,0,0,0.12);
    font-family: "Mulish", sans-serif;
    color: var(--ink);
  }
  .brand {
    position: absolute;
    left: 36px;
    top: 72px;
    display: flex;
    align-items: center;
    gap: 18px;
  }
  .brand-square {
    width: 62px;
    height: 62px;
    background: var(--navy);
  }
  .brand-name {
    font-size: 46px;
    font-weight: 700;
    color: var(--navy);
    letter-spacing: 0.5px;
  }
  .contact {
    position: absolute;
    left: 797px;
    top: 66px;
    height: 126px;
    border-left: 2px solid var(--red);
    padding-left: 14px;
    font-size: 19px;
    line-height: 24px;
    color: #1a1a1a;
  }
  .contact-address { margin: 0 0 12px; }
  .contact-line {
    display: flex;
    align-items: center;
    gap: 14px;
    height: 27px;
  }
  .contact-line svg { width: 18px; height: 18px; fill: var(--red); }
  .date {
    position: absolute;
    right: 42px;
    top: 352px;
    font-size: 21px;
    color: #1a1a1a;
  }
  .recipient {
    position: absolute;
    left: 40px;
    top: 366px;
    font-size: 18.5px;
    line-height: 27px;
  }
  .recipient p { margin: 0; }
  .body-copy {
    position: absolute;
    left: 42px;
    top: 480px;
    width: 987px;
    font-size: 18.5px;
    line-height: 27.2px;
    text-align: justify;
  }
  .body-copy p { margin: 0 0 27px; }
  .closing {
    position: absolute;
    left: 38px;
    top: 1244px;
    font-size: 22px;
    color: #1a1a1a;
  }
  .signature {
    position: absolute;
    left: 38px;
    top: 1284px;
    width: 118px;
    height: 36px;
    background: linear-gradient(90deg, var(--signature-tone), #f0f0f0);
    border-radius: 4px;
  }
</style>
</head>
<body>
<div class="canvas">
  <div class="letterhead">
    <div class="brand">
      <div class="brand-square"></div>
      <div class="brand-name">Marwick Law</div>
    </div>

    <div class="contact">
      <p class="contact-address">1475 Calloway Street,<br>Suite 210, Houston,<br>Texas 77041</p>
      <div class="contact-line">
        <svg viewBox="0 0 24 24" aria-hidden="true"><path d="M6.6 10.8a15.1 15.1 0 0 0 6.6 6.6l2.2-2.2c.3-.3.7-.4 1-.2 1.1.4 2.3.6 3.6.6.6 0 1 .4 1 1V20c0 .6-.4 1-1 1A17 17 0 0 1 3 4c0-.6.4-1 1-1h3.5c.6 0 1 .4 1 1 0 1.3.2 2.5.6 3.6.1.3 0 .7-.2 1z"/></svg>
        <span>832-361-9027</span>
      </div>
      <div class="contact-line">
        <svg viewBox="0 0 24 24" aria-hidden="true"><path d="M7 3h10v5H7zM4 9h16a2 2 0 0 1 2 2v6h-4v4H6v-4H2v-6a2 2 0 0 1 2-2zm4 7v3h8v-3z"/></svg>
        <span>832-614-7359</span>
      </div>
    </div>

    <div class="date">DATE:05-Jan-2022</div>

    <div class="recipient">
      <p>Mr/s</p>
      <p>First Name and Last Name</p>
      <p>Company Name</p>
      <p>Address</p>
    </div>

    <div class="body-copy">
      <p>Lorem ipsum dolor sit amet,consectetur adipiscing sed do eiusmod tempor incididunt laboreet dolore magna aliqua.Ut enim ad minim.veniam, quis nostrud exercitation ullamco laboris nisi ut aliquip exea commodo consequat.Lorem ipsum dolor sit amet,consectetur adipiscing sed do eiusmod tempor incididunt.labore et dolore magna aliqua. Ut enim</p>
      <p>Lorem ipsum dolor sit amet, consectetur adipiscing sed do eiusmod tempor incididunt labore et dolore magna aliqua. Ut enim ad minim veniam, quis nostrud exercitation ullamco laboris nisi ut aliquip exea commodo consequat.Duis aute irure dolor in reprehenderit in voluptate velit esse cillum irure dolor in reprehenderit in voluptate velit esse irure</p>
      <p>Lorem ipsum dolor sit amet, consectetur adipiscing sed do eiusmod tempor incididunt labore et dolore magna aliqua. consequat. Duis aute irure dolor in.reprehenderit in voluptate velit esse cillum dolore eu fugiat nulla pariatur. Excepteur sint occaecat cupidatat non proident, sunt in culpa qui officia deserunt mollit,</p>
      <p>Lorem ipsum dolor sit amet, consectetur adipiscing sed do eiusmod tempor incididunt labore et dolore magna aliqua. Ut enim Lorem ipsum dolor sit amet, consectetur adipiscing sed do eiusmod tempor incididunt labore et dolore magna aliqua. Ut enim Lorem ipsum aliqua.ipsum</p>
      <p>Lorem ipsum dolor sit amet, consectetur adipiscing sed do eiusmod tempor incididunt labore et dolore magna aliqua. Ut enim ad minim veniam, quis nostrud exercitation ullamco laboris nisi ut aliquip exea commodo consequat.Duis aute irure dolor in reprehenderit in voluptate velit esse cillum irure dolor in reprehenderit in voluptate velit esse irure</p>
      <p>Lorem ipsum dolor sit amet, consectetur adipiscing sed do eiusmod tempor incididunt labore et dolore magna aliqua. Ut enim ad minim veniam, quis nostrud exercitation ullamco laboris nisi ut aliquip exea commodo consequat.Duis aute irure dolor in reprehenderit in voluptate velit esse cillum irure dolor in reprehenderit in voluptate velit esse irure</p>
    </div>

    <div class="closing">Regards</div>
    <div class="signature" role="img" aria-label="Handwritten signature of the sender"></div>
  </div>
</div>
</body>
</html>
```